Redesign of business card for Cedar Ridge Mechanical

We are looking for a new design for our business cards for Cedar Ridge Mechanical. We are a plumbing & HVAC construction company, operating on the West Coast of Canada and USA. Logo attached.
Industry/Entity Type
Construction - Plumbing & HVAC
Contact Information for Business Card
Name, address, phone numbers, email, website address
Look and feel
Each slider illustrates characteristics of the customer's brand and the style your logo design should communicate.

```html
<!DOCTYPE html>
<html lang="en">
<head>
<meta charset="utf-8">
<title>Cedar Ridge Mechanical – Business Cards</title>
<link href="https://fonts.googleapis.com/css2?family=Cabin:wght@400;500;700&display=swap" rel="stylesheet">
<style>
  :root {
    --backdrop: #3a3a3c;
    --card: #ffffff;
    --card-shade: #ececec;
    --ink: #1e1a1a;
    --ink-soft: #4a4646;
    --rule: #9a9a9a;
    --ghost: #e2e2e2;
  }
  * { box-sizing: border-box; margin: 0; padding: 0; }
  html, body {
    width: 1200px; height: 900px; overflow: hidden;
    background: var(--backdrop);
    font-family: "Cabin", "Gill Sans", sans-serif;
    color: var(--ink);
  }
  .canvas { position: relative; width: 1200px; height: 900px; }
  .card {
    position: absolute; left: 240px;
    width: 720px; height: 411px;
    background: linear-gradient(135deg, var(--card) 0%, var(--card) 55%, var(--card-shade) 100%);
    border-radius: 34px;
    overflow: hidden;
  }
  .card--services { top: 34px; }
  .card--contact { top: 466px; }

  .brand {
    position: absolute; display: flex; align-items: center; gap: 14px;
    font-weight: 700; font-size: 30px; line-height: 1.05; color: var(--ink);
    text-transform: uppercase; letter-spacing: 1px;
  }
  .brand__mark { width: 30px; height: 30px; background: var(--ink); flex: none; }
  .card--services .brand { left: 56px; top: 160px; }
  .card--contact .brand { left: 56px; top: 64px; }

  .services {
    position: absolute; right: 60px; top: 92px; text-align: right;
    list-style: none; font-size: 19px; line-height: 1.42; color: var(--ink-soft);
  }
  .services__title { font-weight: 700; font-size: 22px; color: var(--ink); letter-spacing: .5px; margin-bottom: 4px; }
  .services li::after { content: " ✓"; color: var(--ink); font-size: 15px; }

  .ghost-name {
    position: absolute; right: 28px; top: 20px; text-align: right;
    font-weight: 700; font-size: 62px; line-height: 1; color: var(--ghost);
    text-transform: uppercase; letter-spacing: 2px;
  }

  .person { position: absolute; right: 360px; top: 262px; text-align: right; }
  .person__role { font-size: 19px; color: var(--ink-soft); }
  .person__name { font-size: 25px; font-weight: 700; text-transform: uppercase; letter-spacing: .5px; }

  .divider { position: absolute; left: 382px; top: 214px; width: 1px; height: 134px; background: var(--rule); }

  .contacts { position: absolute; left: 400px; top: 218px; list-style: none; font-size: 18px; line-height: 1.5; color: var(--ink); }
  .contacts li { display: flex; align-items: flex-start; gap: 9px; }
  .contacts svg { width: 16px; height: 16px; margin-top: 5px; flex: none; fill: var(--ink); }
  .contacts .address { line-height: 1.3; padding-top: 2px; }
</style>
</head>
<body>
<main class="canvas">

  <section class="card card--services">
    <div class="brand"><span class="brand__mark"></span><span>Cedar Ridge<br>Mechanical</span></div>
    <ul class="services">
      <li class="services__title" style="list-style:none">OUR SERVICES</li>
      <li>Pipefitting Systems</li>
      <li>Design Build</li>
      <li>Maintenance</li>
      <li>Fire Protection</li>
      <li>Control Systems</li>
      <li>Energy Recovery &amp; High Efficiency Systems</li>
      <li>Plumbing</li>
      <li>HVAC</li>
    </ul>
  </section>

  <section class="card card--contact">
    <div class="ghost-name" aria-hidden="true">Cedar Ridge<br>Mechanical</div>
    <div class="brand"><span class="brand__mark"></span><span>Cedar Ridge<br>Mechanical</span></div>

    <div class="person">
      <p class="person__role">President/Founder</p>
      <p class="person__name">Daniel Whitcomb</p>
    </div>

    <div class="divider"></div>

    <ul class="contacts">
      <li>
        <svg viewBox="0 0 24 24" aria-hidden="true"><path d="M6.6 10.8a15.1 15.1 0 0 0 6.6 6.6l2.2-2.2a1 1 0 0 1 1-.25 11.4 11.4 0 0 0 3.6.57 1 1 0 0 1 1 1V20a1 1 0 0 1-1 1A17 17 0 0 1 3 4a1 1 0 0 1 1-1h3.5a1 1 0 0 1 1 1c0 1.25.2 2.45.57 3.57a1 1 0 0 1-.25 1z"/></svg>
        <span>604-555-0148</span>
      </li>
      <li>
        <svg viewBox="0 0 24 24" aria-hidden="true"><path d="M2 5h20v14H2zm2 2v.5l8 5 8-5V7l-8 5z"/></svg>
        <span>info@cedarridgemech.com</span>
      </li>
      <li>
        <svg viewBox="0 0 24 24" aria-hidden="true"><path d="M12 2a10 10 0 1 0 0 20 10 10 0 0 0 0-20zm6.9 9h-3a15 15 0 0 0-1.3-6 8 8 0 0 1 4.3 6zM12 4.1c.9 1.3 1.8 3.6 1.9 6.9h-3.8c.1-3.3 1-5.6 1.9-6.9zM9.4 5a15 15 0 0 0-1.3 6h-3a8 8 0 0 1 4.3-6zm-4.3 8h3a15 15 0 0 0 1.3 6 8 8 0 0 1-4.3-6zm6.9 6.9c-.9-1.3-1.8-3.6-1.9-6.9h3.8c-.1 3.3-1 5.6-1.9 6.9zm2.6-.9a15 15 0 0 0 1.3-6h3a8 8 0 0 1-4.3 6z"/></svg>
        <span>www.cedarridgemech.com</span>
      </li>
      <li>
        <svg viewBox="0 0 24 24" aria-hidden="true"><path d="M12 2a7 7 0 0 0-7 7c0 5.2 7 13 7 13s7-7.8 7-13a7 7 0 0 0-7-7zm0 9.5A2.5 2.5 0 1 1 12 6.5a2.5 2.5 0 0 1 0 5z"/></svg>
        <span class="address">2150 Harbor Line Rd.,<br>Suite #410 Portland, OR 97209</span>
      </li>
    </ul>
  </section>

</main>
</body>
</html>
```